Church Offering Envelope for receive weekly offerings

I need the front of an 6 3/4 envelope designed to be a church offering envelope. Our color palette is CMYK, 1a56b7, e8da7e, 19a3a3, 40c7f1, e7282d.
I need all of the text information carried forward from our old envelope (see attached) but the new style needs to be modern and flat. (Don't want another dove and clouds theme) I need a 1/4 border on all four sides as envelopes cannot be printed full bleed.
Logo is attached
Target Market(s)
Church
Industry/Entity Type
Church
Font styles to use
Sans Serif
Requirements
Must have
- must adhere to the color palette is CMYK, 1a56b7, e8da7e, 19a3a3, 40c7f1, e7282d.
- I need all of the text information carried forward from our old envelope (see attached)

```html
<!DOCTYPE html>
<html lang="en">
<head>
<meta charset="utf-8">
<title>Living Grace Ministries – Offering Envelope</title>
<link rel="stylesheet" href="https://fonts.googleapis.com/css2?family=Questrial&display=swap">
<style>
  :root {
    --royal: #1a56b7;
    --sand: #e8da7e;
    --teal: #19a3a3;
    --sky: #40c7f1;
    --red: #e7282d;
    --ink: #1d2433;
    --rule: #5a6275;
    --paper: #ffffff;
    --panel: #fdfbf2;
  }
  * { box-sizing: border-box; margin: 0; padding: 0; }
  html, body {
    width: 1200px; height: 638px; overflow: hidden;
    background: var(--paper);
  }
  .envelope {
    position: relative;
    width: 1200px; height: 638px;
    padding: 0.25in;
    background: var(--paper);
    font-family: "Questrial", "Century Gothic", sans-serif;
    color: var(--ink);
    overflow: hidden;
  }
  .print-area {
    position: relative;
    width: 100%; height: 100%;
    background: var(--panel);
    overflow: hidden;
  }
  .header-band {
    position: absolute; left: 0; top: 0; right: 0; height: 190px;
    background: var(--royal);
  }
  .accent-stripes {
    position: absolute; left: 0; right: 0; top: 190px; height: 20px;
    display: flex; flex-direction: column;
  }
  .accent-stripes span { flex: 1; }
  .accent-stripes .s1 { background: var(--teal); }
  .accent-stripes .s2 { background: var(--sky); }
  .accent-stripes .s3 { background: var(--sand); }
  .accent-stripes .s4 { background: var(--red); }

  .verse {
    position: absolute; left: 20px; top: 56px;
    font-size: 24px; line-height: 24px;
    color: var(--paper);
  }
  .verse span { display: block; padding-left: 4px; }
  .verse span:first-child { padding-left: 0; }

  .brand {
    position: absolute; left: 758px; top: 60px;
    display: flex; align-items: center; gap: 12px;
    font-size: 31px; color: var(--sand); letter-spacing: 1px;
    white-space: nowrap;
  }
  .brand-dot {
    width: 16px; height: 16px; border-radius: 50%;
    background: var(--red); flex: none;
  }

  .field {
    position: absolute; font-size: 31px; line-height: 1;
    display: flex; align-items: flex-end; white-space: nowrap;
  }
  .field .blank {
    border-bottom: 2px dashed var(--rule);
    margin-left: 4px; margin-bottom: 4px; height: 1px;
  }
  .checkbox {
    display: inline-block; width: 22px; height: 22px;
    border: 2px solid var(--royal); margin-right: 4px; margin-bottom: 3px;
    flex: none;
  }
  .name-field { left: 35px; top: 382px; }
  .name-field .blank { width: 716px; }
  .tithe-field { left: 35px; top: 468px; }
  .tithe-field .blank { width: 222px; }
  .media-field { left: 483px; top: 468px; }
  .media-field .checkbox { margin-right: 10px; }
  .media-field .blank { width: 180px; }

  .notice {
    position: absolute; left: 114px; top: 552px;
    font-size: 25px; line-height: 1; white-space: nowrap;
    color: var(--royal);
  }
</style>
</head>
<body>
<main class="envelope">
  <div class="print-area">
    <div class="header-band"></div>
    <div class="accent-stripes">
      <span class="s1"></span><span class="s2"></span><span class="s3"></span><span class="s4"></span>
    </div>

    <p class="verse">
      <span>“Honour the LORD with thy substance,</span>
      <span>and with the firstfruits</span>
      <span>of all thine increase:”;</span>
      <span>Prov 3:9</span>
    </p>

    <div class="brand"><span class="brand-dot"></span>Living Grace Ministries</div>

    <div class="field name-field">Name:<span class="blank"></span></div>
    <div class="field tithe-field"><span class="checkbox"></span>Tithe/Offering<span class="blank"></span></div>
    <div class="field media-field"><span class="checkbox"></span>Radio/Webcast<span class="blank"></span></div>

    <p class="notice">Living Grace Ministries does not receive restricted funds in amounts less than $10,000</p>
  </div>
</main>
</body>
</html>
```